Kestrel Baseball & Softball Camp 2017

Design a flyer that will promote our 2017 summer camp for boys and girls softball.

Weeks of
July 10th - 14th
July 17th - 21st.

Players ages 5 - 11.
Full day = 9:30am - 2:30pm half day = 9:30am - 11:30am.
$295 / full day : $195/ half day

Hosted by "Kestrel Baseball" affiliated with the Harbor Comets Travel Baseball & Softball Club and the Maple Ridge Youth League,

Camp Location MRYL, Route 9C Birch Hollow.

PHone 555-240-7813, email info@kestrelball.example

The color should be "Red white and blue color scheme" with dates and location standing out. Kestrel Logo should be prominent MRYL and Comets smaller and secondary.

Feel free to use stock photo's if available. visit www.harborcomets.example for more pictures and there are links for the 2017 summer camp there with possibly some more information.

Target Market(s)

to catch the eye of parents of players ages 5 - 11 already at little league or shopping in local stores

Colors
ec1f27
0355a3
ffffff

Requirements
Must have
• red white and blue design,
• Kestrel logo and summer camp prominent so it catches the eye and explains what it is right away.
• the comets and maple ridge logo's a the bottom showing the affiliation.
Nice to have
• stock photo's or something showing players having a great time or a beautiful ballpark
Should not have
• to much clutter or hard to figure out what it's for

```html
<!DOCTYPE html>
<html lang="en">
<head>
<meta charset="utf-8">
<title>Kestrel Softball Summer Camp 2017</title>
<link href="https://fonts.googleapis.com/css2?family=Bebas+Neue&family=Oswald:wght@500;700&family=Pacifico&family=Kaushan+Script&display=swap" rel="stylesheet">
<style>
  :root{
    --red:#d7282f;
    --navy:#1f3a6e;
    --blue:#0355a3;
    --white:#ffffff;
    --ink:#1d1d1d;
    --sky:#7fa6cf;
    --stands:#9aa9b8;
    --grass:#8fb27a;
    --grass-light:#b9cfa6;
    --dirt:#e8c6a8;
  }
  *{margin:0;padding:0;box-sizing:border-box}
  html,body{width:817px;height:1200px;overflow:hidden;background:var(--white)}
  .flyer{position:relative;width:817px;height:1200px;overflow:hidden;font-family:'Oswald',sans-serif}
  .ballpark{position:absolute;inset:0;
    background:linear-gradient(180deg,var(--sky) 0%,#a9c1da 17%,var(--stands) 26%,#b7bdc4 38%,#c9cfc9 44%,var(--grass-light) 47%,var(--grass) 52%,#a7c394 62%,#d5e3c9 75%,var(--grass-light) 82%,var(--dirt) 84%,#f0d2b8 100%)}
  .header-curve{position:absolute;left:0;top:0;width:817px;height:215px}
  .brand{position:absolute;left:0;right:0;top:62px;display:flex;justify-content:center;align-items:center;gap:12px}
  .brand-dot{width:34px;height:34px;border-radius:50%;background:var(--red)}
  .brand-name{font-family:'Oswald',sans-serif;font-weight:700;font-size:58px;color:var(--red);line-height:1}
  .script-sport{position:absolute;top:292px;left:0;right:0;text-align:center;font-family:'Pacifico',cursive;font-size:48px;color:var(--white)}
  .camp-title{position:absolute;left:50px;top:350px;font-family:'Bebas Neue',sans-serif;font-size:150px;line-height:1;letter-spacing:3px;white-space:nowrap}
  .camp-title .summer{color:var(--red)}
  .camp-title .camp{color:var(--navy)}
  .camp-year{position:absolute;left:715px;top:365px;transform-origin:left top;transform:translateX(60px) rotate(90deg);font-family:'Bebas Neue',sans-serif;font-size:72px;color:var(--white);line-height:1}
  .audience{position:absolute;left:498px;top:478px;font-family:'Kaushan Script',cursive;font-size:19px;color:var(--white)}
  .weeks{position:absolute;left:80px;top:562px;font-family:'Oswald',sans-serif;font-weight:700;font-size:34px;line-height:50px;color:var(--navy);text-transform:uppercase}
  .ages{position:absolute;left:432px;top:604px;display:flex;gap:14px;align-items:flex-start}
  .ages-label{font-weight:700;font-size:33px;line-height:44px;color:var(--navy);text-transform:uppercase}
  .age-badge{position:absolute;left:613px;top:592px;width:138px;height:138px;border-radius:50%;background:var(--navy);color:var(--white);display:flex;align-items:center;justify-content:center;font-weight:500;font-size:38px}
  .hours{position:absolute;left:66px;top:785px;display:flex;gap:12px;align-items:flex-start}
  .hours p{font-weight:700;font-size:23px;line-height:30px;color:var(--red);text-transform:uppercase}
  .cost{position:absolute;left:446px;top:785px;display:flex;gap:10px;align-items:flex-start}
  .cost-label{font-family:'Kaushan Script',cursive;font-size:19px;color:var(--navy);margin-top:8px}
  .cost p{font-weight:700;font-size:23px;line-height:30px;color:var(--navy);text-transform:uppercase}
  .rule-dashed{position:absolute;left:34px;width:750px;border-top:2px dashed #7a7a7a}
  .host-band{position:absolute;left:0;top:885px;width:817px;height:108px;background:linear-gradient(90deg,var(--white) 0%,var(--white) 70%,rgba(255,255,255,.6) 100%)}
  .host-text{position:absolute;left:45px;top:922px;font-weight:500;font-size:11.5px;line-height:16px;color:var(--ink);text-transform:uppercase;letter-spacing:.3px}
  .partner{position:absolute;display:flex;align-items:center;gap:8px;font-weight:700;font-size:22px;color:var(--navy)}
  .partner-shape{width:58px;height:58px;border-radius:50%;background:#cfdcc2}
  .rule-solid{position:absolute;left:34px;top:995px;width:750px;border-top:2px solid var(--ink)}
  .register{position:absolute;left:62px;top:1035px;font-family:'Kaushan Script',cursive;font-size:44px;line-height:50px;color:var(--red);transform:rotate(-9deg)}
  .info{position:absolute;display:flex;gap:10px}
  .info h3{font-family:'Kaushan Script',cursive;font-weight:400;font-size:20px;color:var(--navy);margin-bottom:10px}
  .info p{font-weight:700;font-size:16.5px;line-height:27px;color:var(--ink);text-transform:uppercase}
</style>
</head>
<body>
<div class="flyer">
  <div class="ballpark" role="img" aria-label="Blurred ballpark stadium with blue sky, grandstands, green infield and dirt base path"></div>

  <svg class="header-curve" viewBox="0 0 817 215" aria-hidden="true">
    <path d="M0 0H817V130Q408 260 0 130Z" fill="#ffffff"/>
  </svg>
  <div class="brand">
    <span class="brand-dot"></span>
    <span class="brand-name">Kestrel</span>
  </div>

  <div class="script-sport">softball</div>
  <h1 class="camp-title"><span class="summer">SUMMER</span><span class="camp">CAMP</span></h1>
  <div class="camp-year">2017</div>
  <div class="audience">for boys and girls</div>

  <div class="weeks">
    <p>Weeks of</p>
    <p>July 10th - 14th</p>
    <p>July 17th - 21st.</p>
  </div>

  <div class="ages">
    <svg width="40" height="34" viewBox="0 0 40 34" aria-hidden="true" style="margin-top:6px">
      <g fill="#1f3a6e">
        <circle cx="10" cy="5" r="4"/><rect x="5" y="11" width="10" height="13" rx="2"/><rect x="6" y="22" width="3.5" height="11"/><rect x="10.5" y="22" width="3.5" height="11"/>
        <circle cx="30" cy="5" r="4"/><path d="M24 11h12l3 14H21z"/><rect x="26" y="24" width="3.5" height="9"/><rect x="30.5" y="24" width="3.5" height="9"/>
      </g>
    </svg>
    <div class="ages-label"><p>Players</p><p>Ages</p></div>
  </div>
  <div class="age-badge">5 - 11</div>

  <div class="hours">
    <svg width="32" height="34" viewBox="0 0 32 34" aria-hidden="true" style="margin-top:10px">
      <g fill="none" stroke="#d7282f" stroke-width="3">
        <circle cx="16" cy="19" r="12"/><path d="M12 3h8M16 3v4M16 19l5-5M26 8l3-3"/>
      </g>
    </svg>
    <div><p>Full day = 9:30am - 2:30pm</p><p>Half day = 9:30am - 11:30am.</p></div>
  </div>

  <div class="cost">
    <span class="cost-label">Cost:</span>
    <svg width="32" height="32" viewBox="0 0 32 32" aria-hidden="true" style="margin-top:4px">
      <circle cx="16" cy="16" r="16" fill="#1f3a6e"/>
      <text x="16" y="23" text-anchor="middle" font-family="Oswald, sans-serif" font-weight="700" font-size="20" fill="#ffffff">$</text>
    </svg>
    <div><p>$295 / full day</p><p>$195/ half day</p></div>
  </div>

  <div class="rule-dashed" style="top:877px"></div>
  <div class="host-band"></div>
  <div class="host-text">
    <p>Hosted by "Kestrel Baseball"</p>
    <p>Affiliated with the Harbor Comets Travel Baseball &amp; Softball Club and</p>
    <p>the Maple Ridge Youth League</p>
  </div>
  <div class="partner" style="left:530px;top:920px">Comets</div>
  <div class="partner" style="left:690px;top:908px"><span class="partner-shape"></span></div>
  <div class="rule-solid"></div>
  <div class="rule-dashed" style="top:1010px"></div>

  <div class="register">Register<br>today!</div>

  <div class="info" style="left:262px;top:1032px">
    <svg width="16" height="22" viewBox="0 0 16 22" aria-hidden="true" style="margin-top:4px">
      <path d="M8 0a8 8 0 0 1 8 8c0 6-8 14-8 14S0 14 0 8a8 8 0 0 1 8-8z" fill="#1f3a6e"/><circle cx="8" cy="8" r="3" fill="#f0d2b8"/>
    </svg>
    <div><h3>Camp Location:</h3><p>Camp location MRYL,</p><p>Route 9C Birch Hollow.</p></div>
  </div>

  <div class="info" style="left:516px;top:1028px">
    <svg width="16" height="26" viewBox="0 0 16 26" aria-hidden="true" style="margin-top:2px">
      <rect x="1" y="4" width="14" height="22" rx="3" fill="#1f3a6e"/><rect x="4" y="8" width="8" height="7" fill="#f0d2b8"/><rect x="10" y="0" width="3" height="6" fill="#1f3a6e"/>
    </svg>
    <div><h3>Contact:</h3><p>Phone 555-240-7813, email</p><p>info@kestrelball.example</p></div>
  </div>
</div>
</body>
</html>
```